Heron Loan Partners Business Card

We need a business card design for our mortgage servicing company. In addition to servicing the loans of homeowners, we help homeowners with purchasing their homes and any mortgage refinancing. We would like to see designs that use the colors in the logo attached below (gold-ish yellow and navy blue), and any other design you deem fit! The design should communicate a simpler life with smart mortgages provided by Heron.

```html
<!DOCTYPE html>
<html lang="en">
<head>
<meta charset="utf-8">
<title>Heron Loan Partners Business Card</title>
<link href="https://fonts.googleapis.com/css2?family=Open+Sans:wght@400;600;700&display=swap" rel="stylesheet">
<style>
  :root {
    --stage: #222224;
    --card-dark: #1c1c20;
    --gold: #e2b23c;
    --gold-deep: #c9962a;
    --white: #f4f4f4;
    --muted: #2a2a30;
  }
  * { box-sizing: border-box; margin: 0; padding: 0; }
  html, body { width: 1200px; height: 780px; overflow: hidden; }
  body {
    background: var(--stage);
    font-family: "Open Sans", Arial, sans-serif;
    display: flex;
    align-items: center;
    justify-content: center;
    gap: 60px;
  }
  .card {
    width: 525px;
    height: 300px;
    position: relative;
    overflow: hidden;
    border-radius: 3px;
    box-shadow: 0 18px 40px rgba(0,0,0,0.45);
  }
  .card-front { background: var(--card-dark); color: var(--white); }
  .brand {
    position: absolute; top: 28px; left: 32px;
    display: flex; align-items: center; gap: 10px;
  }
  .brand-mark { width: 16px; height: 16px; background: var(--gold); }
  .brand-name { font-size: 34px; font-weight: 700; color: var(--gold); line-height: 1; }
  .brand-sub {
    position: absolute; top: 70px; left: 58px;
    font-size: 10px; letter-spacing: 3px; color: var(--white); font-weight: 600;
  }
  .brand-emboss {
    position: absolute; bottom: 18px; left: 150px;
    font-size: 84px; font-weight: 700; color: var(--muted); line-height: 1;
  }
  .contact {
    position: absolute; top: 108px; left: 32px;
    font-size: 13px; line-height: 1.55; list-style: none;
  }
  .contact li { display: flex; align-items: center; gap: 8px; }
  .contact svg { width: 11px; height: 11px; fill: var(--gold); flex: none; }
  .contact .address { padding-left: 19px; }
  .person {
    position: absolute; right: 40px; bottom: 60px; text-align: right;
  }
  .person-name { font-size: 26px; font-weight: 700; }
  .person-name .first { color: var(--gold); }
  .person-title { font-size: 14px; color: var(--white); }
  .accent-strip {
    position: absolute; right: 0; bottom: 40px;
    width: 22px; height: 70px; background: var(--gold);
  }
  .card-back {
    background: linear-gradient(135deg, var(--gold) 0%, var(--gold-deep) 100%);
  }
  .back-pattern { position: absolute; inset: 0; }
</style>
</head>
<body>
  <section class="card card-front">
    <div class="brand">
      <span class="brand-mark"></span>
      <span class="brand-name">Heron</span>
    </div>
    <div class="brand-sub">LOAN PARTNERS</div>
    <div class="brand-emboss">Heron</div>
    <ul class="contact">
      <li class="address">418 Cedar Bend Rd. Suite 300</li>
      <li class="address">Brookfield, TX 75310</li>
      <li><svg viewBox="0 0 24 24"><path d="M6.6 10.8a15 15 0 0 0 6.6 6.6l2.2-2.2a1 1 0 0 1 1-.25 11.4 11.4 0 0 0 3.6.57 1 1 0 0 1 1 1V20a1 1 0 0 1-1 1A17 17 0 0 1 3 4a1 1 0 0 1 1-1h3.5a1 1 0 0 1 1 1c0 1.25.2 2.45.57 3.57a1 1 0 0 1-.25 1z"/></svg>(555) 214-0836</li>
      <li><svg viewBox="0 0 24 24"><path d="M2 5h20v14H2zm2 2v.5l8 5 8-5V7z"/></svg>hello@heronloan.com</li>
      <li><svg viewBox="0 0 24 24"><circle cx="12" cy="12" r="10"/></svg>www.heronloan.com</li>
    </ul>
    <div class="person">
      <p class="person-name"><span class="first">Lena</span> Varga</p>
      <p class="person-title">Managing Director</p>
    </div>
    <div class="accent-strip"></div>
  </section>

  <section class="card card-back">
    <div class="back-pattern" role="img" aria-label="Repeating brand pattern in darker gold tones"></div>
  </section>
</body>
</html>
```